Exciting new aperitif brand needs a great label

Vel-Orin is a wonderful rich new premium-priced bitter aperitif, with a deep red colour, from a 100+ year old distillery (1890) near Turin in the Piedmont region of Italy. Inspired by Tessoni, it is perfectly formulated to elevate the classic Bravetti cocktail (and variations on it). It also goes perfectly in a Spritz or a long mixed drink with soda or tonic. The name Vel-Orin is derived from the French for 'peak' and the Italian word for 'love'.

The label, which should take inspiration from Tessoni, but be distinctively different, can incoporate any number of premium label embellishments (foil, embossing, textures etc) and should be no greater than 11cm (height) x 9cm (width) with any core imagery restricted to a width of c.7cm.

The attached mood board should act as inspiration and colour should largely be restricted to reds, blues, whites and perhaps orange. For completeness, the label should note that the ABV is 25% and the bottle size 70cl.

Target Market(s)

21-45yr olds - equal split female/male

Colors
0054AA
0677BA
7BADD7
CADEEF
E8F1F8
0094D4
00A9DD
6FCCEA
C7EBF8
E9F6FB
EE7325
F08F49
F5BC92
FAE3D3
FDF4ED
EB3D1F
EC4F4E
F09395
F8D3D4
FCEDEE

Requirements
Must have
• Great lettering design on the name Vel-Orin

```html
<!DOCTYPE html>
<html lang="en">
<head>
<meta charset="utf-8">
<title>Vel-Orin Bitter Aperitivo Label</title>
<link rel="stylesheet" href="https://fonts.googleapis.com/css2?family=Alfa+Slab+One&family=Zilla+Slab:wght@400;500&display=swap">
<style>
  :root {
    --gold-light: #f7e08a;
    --gold: #e0a83a;
    --gold-deep: #c97a26;
    --copper: #b8682a;
    --teal-light: #22b5a2;
    --teal: #0f8a78;
    --teal-deep: #06604f;
    --navy: #020d2a;
    --navy-mid: #0a1640;
    --white: #ffffff;
    --paper: #f7f7f5;
  }
  html, body {
    margin: 0;
    padding: 0;
    width: 982px;
    height: 1200px;
    overflow: hidden;
    background: #ffffff;
  }
  .label {
    position: relative;
    width: 982px;
    height: 1200px;
  }
  .label svg { display: block; }
  .brand-name, .tagline, .abv {
    font-family: "Alfa Slab One", "Arvo", serif;
  }
  .origin {
    font-family: "Zilla Slab", "Arvo", serif;
  }
</style>
</head>
<body>
<main class="label">
  <svg width="982" height="1200" viewBox="0 0 982 1200" xmlns="http://www.w3.org/2000/svg">
    <defs>
      <linearGradient id="frameGold" x1="0" y1="0" x2="1" y2="1">
        <stop offset="0" stop-color="var(--gold-light)"/>
        <stop offset="0.45" stop-color="var(--gold)"/>
        <stop offset="0.75" stop-color="var(--gold-deep)"/>
        <stop offset="1" stop-color="var(--gold-light)"/>
      </linearGradient>
      <radialGradient id="tealGlow" cx="0.42" cy="0.75" r="0.7">
        <stop offset="0" stop-color="var(--teal-light)"/>
        <stop offset="0.6" stop-color="var(--teal)"/>
        <stop offset="1" stop-color="var(--teal-deep)"/>
      </radialGradient>
      <radialGradient id="navyGlow" cx="0.45" cy="0.4" r="0.6">
        <stop offset="0" stop-color="var(--navy-mid)"/>
        <stop offset="0.7" stop-color="var(--navy)"/>
        <stop offset="1" stop-color="#05050f"/>
      </radialGradient>
      <linearGradient id="lineGold" x1="0" y1="0" x2="1" y2="0">
        <stop offset="0" stop-color="var(--gold-deep)"/>
        <stop offset="0.5" stop-color="var(--gold-light)"/>
        <stop offset="1" stop-color="var(--copper)"/>
      </linearGradient>
      <linearGradient id="textGold" x1="0" y1="0" x2="1" y2="0">
        <stop offset="0" stop-color="#e08a10"/>
        <stop offset="0.4" stop-color="#f0b818"/>
        <stop offset="1" stop-color="#c08528"/>
      </linearGradient>
      <linearGradient id="taglineGold" x1="0" y1="0" x2="1" y2="0">
        <stop offset="0" stop-color="#e8b84a"/>
        <stop offset="0.5" stop-color="#d9a035"/>
        <stop offset="1" stop-color="#ffe27a"/>
      </linearGradient>
      <linearGradient id="ornamentGold" x1="0" y1="0" x2="1" y2="1">
        <stop offset="0" stop-color="var(--gold-light)" stop-opacity="0.7"/>
        <stop offset="1" stop-color="var(--gold-deep)" stop-opacity="0.5"/>
      </linearGradient>
    </defs>

    <rect class="frame" x="0" y="0" width="982" height="1200" fill="url(#frameGold)"/>

    <rect class="field-top" x="13" y="13" width="956" height="400" fill="url(#tealGlow)"/>
    <g class="field-top-lines" stroke="#ffffff" stroke-opacity="0.12" stroke-width="1.5" fill="none">
      <polyline points="13,105 494,-1 969,105"/>
      <polyline points="13,150 494,34 969,150"/>
      <polyline points="13,195 494,68 969,195"/>
      <polyline points="13,245 494,107 969,245"/>
      <polyline points="13,295 494,153 969,295"/>
    </g>

    <rect class="field-bottom" x="13" y="780" width="956" height="407" fill="var(--paper)"/>
    <g class="field-bottom-lines" stroke="url(#lineGold)" fill="none">
      <polyline points="13,893 494,1032 969,893" stroke-width="2.5"/>
      <polyline points="13,945 494,1080 969,945" stroke-width="1.5" stroke-opacity="0.7"/>
      <polyline points="13,995 494,1128 969,995" stroke-width="1.2" stroke-opacity="0.5"/>
      <polyline points="13,1045 494,1176 969,1045" stroke-width="1" stroke-opacity="0.45"/>
      <polyline points="13,1095 494,1224 969,1095" stroke-width="1" stroke-opacity="0.4"/>
    </g>

    <polygon class="corner-ornament" role="img" aria-label="Gold filigree corner ornament" points="34,34 215,34 34,212" fill="url(#ornamentGold)"/>
    <polygon class="corner-ornament" role="img" aria-label="Gold filigree corner ornament" points="948,34 760,34 948,216" fill="url(#ornamentGold)"/>
    <polygon class="corner-ornament" role="img" aria-label="Gold filigree corner ornament" points="40,980 40,1163 220,1163" fill="url(#ornamentGold)"/>
    <polygon class="corner-ornament" role="img" aria-label="Gold filigree corner ornament" points="942,980 942,1163 762,1163" fill="url(#ornamentGold)"/>

    <polygon class="hex-band" points="494,199 982,358 982,834 494,990 0,840 0,351" fill="url(#navyGlow)"/>
    <polygon class="hex-rule" points="493,260 954,398 954,806 493,942 34,809 34,390" fill="none" stroke="url(#lineGold)" stroke-width="3"/>

    <text class="brand-name" x="491" y="650" font-size="148" letter-spacing="4" text-anchor="middle" fill="var(--white)">VEL-ORIN</text>

    <text class="tagline" x="51" y="775" font-size="34" textLength="877" lengthAdjust="spacing" fill="url(#taglineGold)">BITTER APERITIVO</text>

    <text class="origin" x="492" y="1093" font-size="60" font-weight="400" text-anchor="middle" fill="url(#textGold)">Made In Italy</text>

    <text class="abv" x="492" y="1160" font-size="29" text-anchor="middle" letter-spacing="10" fill="url(#textGold)">25% ABV · 70CL</text>
  </svg>
</main>
</body>
</html>
```